Business Cards for IT Consulting Company (Managed Service Provider)

I am looking to have some business cards printed and would like some designs. We are an IT Consulting company based in Vancouver BC. I would like a nice clean and modern look to the cards. I have uploaded all the versions of my logo so parts can be used as needed. Here is a snippit from our website homepage:

Quillbrook Networks Ltd. is an IT Solutions Partner located in Vancouver BC, Canada. We offer IT solutions and support to customers in the greater Vancouver Area. With expertise in Microsoft platforms, as well as Linux and Mac OSX and over 12 years experience in the IT industry, Quillbrook Networks is dedicated to offering our clients top quality service and products. We take pride in the solutions we offer our customers. The greatest compliment a client can give us is to recommend our services.

Quillbrook Networks Ltd. offers a wide range of IT services from onsite service to remote support and managed service solutions. This allows clients to choose the support path that best suits their company’s needs. Supporting many different sized companies from small to enterprise level over the past 12 years Quillbrook Networks has the experience and expertise needed to ensure things run smoothly. Allowing our clients to focus on doing business.

Revolutionizing the way IT services are delivered.

Quillbrook Networks is dedicated to providing our clients with IT solutions that work and grow with them for years to come. This philosophy helps save money in the long run instead of replacing equipment constantly. Far too often IT solutions are not well thought out and while possibly solving the problem at hand, require replacement due to growth or quality within a very short time frame. Quillbrook Networks takes pride in providing solutions that will last and be able to accommodate growth without the need for replacement.

Industry/Entity Type

Information Technology

Contact Information for Business Card

Quillbrook Networks Ltd.
(Employee Name)
Eml: (Employees Email Address)
Web: quillbrook.me
Ph: 604-555-0148

Font styles to use
Serif
Sans Serif

Requirements
Must have
• The Company logo and company colors.
Nice to have
• - Our tag line: "Revolutionizing IT Services" or "Revolutionizing the way IT services are delivered."
• - Also I really like the idea of nature and technology together blending which is sort of where my logo came from so integrating that somehow onto the business cards would be great.

```html
<!DOCTYPE html>
<html lang="en">
<head>
<meta charset="utf-8">
<title>Quillbrook Networks Ltd. – Business Cards</title>
<link rel="stylesheet" href="https://fonts.googleapis.com/css2?family=Arimo:wght@400;700&display=swap">
<style>
  :root {
    --brand-blue: #22aee6;
    --card-white: #ffffff;
    --frame-grey: #8a8d90;
    --ink-grey: #6d6f72;
    --stage: #ecedef;
    --shadow: rgba(0, 0, 0, 0.18);
  }
  * { box-sizing: border-box; margin: 0; padding: 0; }
  html, body {
    width: 1200px;
    height: 950px;
    overflow: hidden;
    background: var(--stage);
    font-family: "Arimo", Arial, sans-serif;
  }
  .stage { position: relative; width: 1200px; height: 950px; }

  .card {
    position: absolute;
    width: 620px;
    height: 354px;
    overflow: hidden;
    box-shadow: 0 8px 22px var(--shadow);
  }

  /* Front card */
  .card--front {
    left: 90px;
    top: 80px;
    background: var(--brand-blue);
    color: var(--card-white);
  }
  .front-logo {
    position: absolute;
    left: 150px;
    top: 108px;
    display: flex;
    align-items: center;
    gap: 18px;
  }
  .logo-square {
    width: 52px;
    height: 52px;
    border: 3px solid currentColor;
  }
  .logo-name {
    font-weight: 700;
    line-height: 1;
  }
  .logo-name .word { display: block; font-size: 54px; letter-spacing: 0.5px; }
  .logo-name .suffix { display: block; font-size: 19px; letter-spacing: 1.5px; margin-top: 4px; }
  .tagline {
    position: absolute;
    left: 0;
    right: 0;
    top: 250px;
    text-align: center;
    font-size: 14px;
    font-weight: 700;
  }

  /* Back card */
  .card--back {
    left: 490px;
    top: 500px;
    background: var(--card-white);
  }
  .back-logo {
    position: absolute;
    left: 60px;
    top: 130px;
    display: flex;
    align-items: center;
    gap: 14px;
    color: var(--brand-blue);
  }
  .back-logo .logo-square { width: 40px; height: 40px; }
  .back-logo .logo-name .word { font-size: 42px; }
  .back-logo .logo-name .suffix { font-size: 15px; }

  .contact-panel { position: absolute; inset: 0; }

  .contact {
    position: absolute;
    right: 26px;
    top: 58px;
    text-align: right;
    color: var(--card-white);
    font-size: 14px;
    line-height: 1.5;
  }
  .contact .name { font-size: 19px; font-weight: 700; margin-bottom: 14px; padding-right: 24px; }
  .contact .address { margin-bottom: 12px; padding-right: 24px; }
  .contact-line { display: flex; justify-content: flex-end; align-items: center; gap: 8px; }
  .contact-line svg { width: 16px; height: 16px; flex: none; }
</style>
</head>
<body>
<main class="stage">

  <section class="card card--front" aria-label="Business card front">
    <div class="front-logo">
      <span class="logo-square" aria-hidden="true"></span>
      <span class="logo-name">
        <span class="word">quillbrook</span>
        <span class="suffix">NETWORKS LTD.</span>
      </span>
    </div>
    <p class="tagline">Revolutionizing IT Services</p>
  </section>

  <section class="card card--back" aria-label="Business card back">
    <div class="back-logo">
      <span class="logo-square" aria-hidden="true"></span>
      <span class="logo-name">
        <span class="word">quillbrook</span>
        <span class="suffix">NETWORKS LTD.</span>
      </span>
    </div>

    <svg class="contact-panel" viewBox="0 0 620 354" aria-hidden="true">
      <polygon points="402,20 640,20 640,334 402,334 316,177" fill="var(--frame-grey)"/>
      <polygon points="407,28 640,28 640,326 407,326 326,177" fill="var(--card-white)"/>
      <polygon points="411,33 640,33 640,321 411,321 333,177" fill="var(--brand-blue)"/>
    </svg>

    <div class="contact">
      <p class="name">Mara Ellison</p>
      <p class="address">2190 Alder Crescent<br>Vancouver, BC V5K 0A1</p>
      <p class="contact-line">604 555 0148
        <svg viewBox="0 0 16 16" aria-hidden="true"><path d="M2 5c0-2 2-3 6-3s6 1 6 3v1h-3V5H5v1H2z M4 7h8l2 6H2z" fill="#fff"/><circle cx="8" cy="10" r="1.6" fill="var(--brand-blue)"/></svg>
      </p>
      <p class="contact-line">mara@quillbrook.me
        <svg viewBox="0 0 16 16" aria-hidden="true"><rect x="1.5" y="3.5" width="13" height="9" fill="#fff"/><path d="M1.5 3.5 8 9l6.5-5.5" stroke="var(--brand-blue)" stroke-width="1.2" fill="none"/></svg>
      </p>
      <p class="contact-line">www.quillbrook.me
        <svg viewBox="0 0 16 16" aria-hidden="true"><circle cx="8" cy="8" r="6.5" fill="#fff"/><ellipse cx="8" cy="8" rx="2.6" ry="6.5" stroke="var(--brand-blue)" fill="none"/><path d="M1.5 8h13" stroke="var(--brand-blue)"/></svg>
      </p>
    </div>
  </section>

</main>
</body>
</html>
```